Online Shop Maren

We need a web design for an online shop, called "Lirvo Dune Jewels". The shop should have an extraordinary, elegant look, as shown in the Quellwick Advertising Picture in our Briefing.pdf (attached). Please have a look at our Briefing regarding website colours, background ideas, and elements to be included. The online shop is about professional jewellery design pieces, where each piece is handmade of high quality materials, also unique pieces and unique editions possible. It should attract extraordinary people and visualize that its a very individual and unique design jewellery. You can get an idea of whom it should attract by reading our target group. Colours to be used are jewellery-Velvet red, Black / anthracite, exclusive colours, silverish-white, bronze-brown and golden.

Please play around when designing with the image pictures we attach, preferably more vertical pictures, no panoramic pictures like in Brovenka Shop. Also include the BLACK logo of lirvo dune. We include the SITEMAP in the briefing and also another folder with product pictures you can use for the draft.

Regarding Functions, the store will have the SAME (technical) functions as this page:http://www.brovenka-shop.eu/ - using the "most famous" products/categories for the starting page, going into individual product pages by clicking these images and then leading to a detailed page for one product only.

Target Market(s)

Jewellery-lovers, who appreciate extraordinary things, creative economy/fashion-industries, stylists, Style consultants, outfitter, theatres, operas, production sites, Cocktail-, Dinner and Bridefashion, exclusive traditional costume stores, dancesports and tango argento dancers

Industry/Entity Type

Shop

Requirements
Must have
• Must include:
• Colours as per briefing
• Background ideas/images as per briefing/pictures sent
• Sitemap as per briefing
• Social buttons
• Logo
• Design for 3 pages: Starting page showing big images, attractive design and the 4 popular categories
• Subpage with different products of one category (i.e. bracelets)
• Detail page with one individual product only
Should not have
• no fresh, playful colours like yellow, orange, green, blue
• no cheap design, no panorama pictures

```html
<!DOCTYPE html>
<html lang="en">
<head>
<meta charset="utf-8">
<title>Lirvo Dune Jewels</title>
<link href="https://fonts.googleapis.com/css2?family=Open+Sans:wght@400;600;700&family=Antonio:wght@100&display=swap" rel="stylesheet">
<style>
:root{
  --paper:#f3ece4;
  --blush:#ead5ca;
  --blush-deep:#e2bfae;
  --ink:#111;
  --grey:#6d6d6d;
  --line:#c9c9c9;
  --white:#fff;
  --accent-text:#e2a995;
}
*{box-sizing:border-box;margin:0;padding:0}
html,body{width:1200px;height:1195px;overflow:hidden}
body{position:relative;background:var(--paper);font-family:"Open Sans",Verdana,sans-serif;color:var(--ink)}
.abs{position:absolute}
.topbar{left:167px;top:0;width:865px;height:19px;background:var(--blush)}
.topbar a{position:absolute;top:4px;font-size:9px;color:#444;text-decoration:none}
.topbar .shop{font-weight:700}
.login{left:784px;top:3px;font-size:10px}
.bag{left:889px;top:0;width:139px;height:27px;background:var(--ink);color:var(--white);font-size:11px;display:flex;align-items:center;justify-content:center;gap:6px}
.alerts{left:172px;top:37px;font-size:9px;line-height:11px}
.alerts .ship{color:var(--accent-text);letter-spacing:1px;font-size:8.5px}
.brand{left:440px;top:38px;width:320px;text-align:center;font-size:32px;line-height:36px;letter-spacing:.5px}
.brand small{display:block;font-size:12px;line-height:16px;letter-spacing:.5px;margin-top:6px}
.search{left:822px;top:41px;width:205px;height:20px;background:var(--white);border:1px solid #ddd;font-size:7px;color:#aaa;padding:5px 8px}
.search svg{position:absolute;right:4px;top:4px}
.join{left:893px;top:66px;font-size:10px;display:flex;gap:5px;align-items:center}
.join i{display:inline-block;width:10px;height:10px;border-radius:50%;background:#999}
.join b{display:inline-block;width:32px;height:10px;background:#999}
.nav{left:0;top:105px;width:1200px;font-size:11px;letter-spacing:1px}
.nav span{position:absolute}
.panel{left:167px;top:126px;width:865px;height:838px;background:var(--white);border:1px solid #333;box-shadow:0 8px 16px rgba(0,0,0,.18)}
.hero{left:0;top:0;width:657px;height:501px;background:linear-gradient(100deg,#b8a89a 0%,#e6dde2 30%,#9fb9b6 50%,#8b8088 70%,#d7c9d8 100%)}
.side{left:657px;top:0;width:207px;height:501px;background:var(--white);border-left:1px solid #333;overflow:hidden}
.side .orn{position:absolute;right:0;bottom:0;width:207px;height:420px;background:linear-gradient(200deg,transparent 30%,rgba(226,191,174,.55) 70%,rgba(226,191,174,.85))}
.side .shoplink{position:absolute;left:91px;top:8px;font-size:10px;letter-spacing:1px}
.side h1{position:absolute;left:6px;top:88px;font-family:"Antonio",sans-serif;font-weight:100;font-size:42px;line-height:60px;letter-spacing:1px;white-space:nowrap}
.side p{position:absolute;left:6px;width:200px;font-size:11.5px;line-height:13px}
.side .cta{position:absolute;left:6px;top:430px;background:var(--ink);color:var(--white);font-size:8px;padding:1px 7px;font-weight:700}
.dots{left:395px;top:510px;display:flex;gap:7px}
.dots i{width:9px;height:9px;border-radius:50%;background:#ddd}
.dots i:first-child{background:#aaa}
.news-title{left:6px;top:561px;width:842px;height:20px;text-align:center;font-size:12px;letter-spacing:2px}
.news-title::before,.news-title::after{content:"";position:absolute;top:9px;width:347px;border-top:1px solid var(--line)}
.news-title::before{left:0}.news-title::after{right:0}
.arrow{top:652px;font-size:20px}
.item{position:absolute}
.item .ph{height:141px}
.item .nm{font-size:11px;margin-top:6px}
.item .pr{font-size:11px;font-weight:700;margin-top:11px}
.item .buy{display:inline-block;background:var(--ink);color:var(--white);font-size:11px;padding:0 9px;margin-top:8px;line-height:14px}
.foot h3{position:absolute;top:989px;font-size:11px;letter-spacing:1px;font-weight:700}
.foot ul{position:absolute;top:1021px;list-style:none;font-size:10px;line-height:16.4px;color:var(--grey);letter-spacing:.5px}
.foot .news-txt{left:793px;top:1015px;font-size:8.5px;line-height:11px;color:var(--grey)}
.email{left:791px;top:1067px;width:216px;height:23px;background:#e4ddd6;font-size:8px;color:#aaa;padding:6px}
.sub{left:791px;top:1095px;width:75px;height:16px;background:var(--blush);font-size:10px;padding:1px 6px}
.copy{left:171px;top:1183px;font-size:8.5px}
.badge{left:937px;top:1168px;width:92px;height:25px;border-radius:12px;background:#ddd5cc}
</style>
</head>
<body>
<div class="abs topbar">
  <a class="shop" style="left:5px">Online Shop</a>
  <a style="left:74px">Info &amp; Facts</a>
  <a style="left:146px">Partner</a>
  <a style="left:193px">About me</a>
  <a style="left:252px">Contact</a>
</div>
<div class="abs login">Log In / Join now</div>
<div class="abs bag">SHOPPING BAG (0)
  <svg width="10" height="12" viewBox="0 0 10 12"><rect x="0" y="3" width="10" height="9" fill="#fff"/><path d="M3 4V2a2 2 0 0 1 4 0v2" stroke="#fff" fill="none"/></svg>
</div>

<div class="abs alerts">Email Alerts &amp; Updates &nbsp;subscribe
  <svg width="18" height="10" viewBox="0 0 18 10"><rect x=".5" y=".5" width="17" height="9" fill="none" stroke="#555"/><path d="M.5 .5 9 6 17.5 .5" fill="none" stroke="#555"/></svg><br>
  <span class="ship">FREE SHIPPING ON ORDERS OVER $100!</span>
</div>
<div class="abs brand">Lirvo Dune<small>♦ Jewels ♦</small></div>
<div class="abs search">Enter Keyword or Web ID
  <svg width="10" height="10" viewBox="0 0 10 10"><circle cx="4" cy="4" r="3" stroke="#333" fill="none" stroke-width="1.4"/><path d="M6.2 6.2 9 9" stroke="#333" stroke-width="1.4"/></svg>
</div>
<div class="abs join">Join us on: <i></i><i></i><b></b></div>

<div class="abs nav">
  <span style="left:239px">HOME</span>
  <span style="left:323px">NEW JEWELRY</span>
  <span style="left:446px">NECKLACES</span>
  <span style="left:570px">BRACELETS</span>
  <span style="left:695px">RINGS</span>
  <span style="left:793px">EARRINGS</span>
  <span style="left:891px">GIFTS</span>
</div>

<main class="abs panel">
  <div class="abs hero" role="img" aria-label="Model in a lace dirndl with a mint apron standing by a window, wearing bracelets"></div>
  <aside class="abs side">
    <div class="orn" role="img" aria-label="Soft blush floral ornament"></div>
    <span class="shoplink">SHOP BRACELETS</span>
    <h1>Atelier<br>Maren Velder</h1>
    <p style="top:243px">Lorem ipsum dolor sit amet, <b>consectetur adipisicing</b> elit, sed do eiusmod tempor incididunt ut labore et dolore magna aliqua.</p>
    <p style="top:308px">Ut enim ad minim veniam, quis nostrud exercitation <b>ullamco</b> laboris nisi ut aliquip ex ea commodo consequat.</p>
    <span class="cta">VIEW THE COLLECTION</span>
  </aside>
  <div class="abs dots"><i></i><i></i><i></i><i></i><i></i></div>
  <div class="abs news-title">WHAT’S NEW</div>
  <span class="abs arrow" style="left:10px">«</span>
  <span class="abs arrow" style="left:840px">»</span>

  <div class="item" style="left:51px;top:591px;width:190px">
    <div class="ph" role="img" aria-label="Black beaded statement necklace on a white bust" style="background:linear-gradient(#111,#2a2a2a 40%,#e9e9e9 55%,#111)"></div>
    <div class="nm">Lorem ipsum dolor sit amet</div><div class="pr">£834.99</div><span class="buy">BUY NOW</span>
  </div>
  <div class="item" style="left:255px;top:591px;width:165px">
    <div class="ph" role="img" aria-label="Silver beaded bib necklace on black" style="background:radial-gradient(ellipse at 50% 40%,#9a9a9a,#222 70%)"></div>
    <div class="nm">Lorem ipsum dolor sit amet</div><div class="pr">£834.99</div><span class="buy">BUY NOW</span>
  </div>
  <div class="item" style="left:439px;top:593px;width:184px">
    <div class="ph" style="height:139px;background:radial-gradient(ellipse at 50% 45%,#cfc6bd,#3a3633 65%,#111)" role="img" aria-label="Crystal and silver beaded collar necklace"></div>
    <div class="nm">Lorem ipsum dolor sit amet</div><div class="pr">£834.99</div><span class="buy">BUY NOW</span>
  </div>
  <div class="item" style="left:636px;top:592px;width:179px">
    <div class="ph" style="height:140px;background:radial-gradient(ellipse at 55% 55%,#d8cfa8,#3c3c3c 55%,#151515)" role="img" aria-label="Golden crystal teardrop pendant on a pearl strand"></div>
    <div class="nm">Lorem ipsum dolor sit amet</div><div class="pr">£834.99</div><span class="buy">BUY NOW</span>
  </div>
</main>

<footer class="foot">
  <h3 style="left:194px">PAYMENT &amp; SHIPPING</h3>
  <h3 style="left:415px">CUSTOMER SERVICE</h3>
  <h3 style="left:631px">PRESS</h3>
  <h3 style="left:793px">GET ON THE LIST</h3>
  <ul style="left:194px"><li>CardNova</li><li>Payvia</li><li>WalletPass</li><li>Direct Debit</li><li>Immediately transfer</li><li>&nbsp;</li><li>Postrix</li><li>Kurvo Express</li></ul>
  <ul style="left:415px"><li>FAQs</li><li>Terms and Conditions</li><li>Shipping and Charges</li><li>Returns</li><li>Right of withdrawal</li><li>Privacy Policy</li><li>Ring Size Chart</li><li>Contact</li><li>Review</li></ul>
  <ul style="left:631px"><li>Stylene</li><li>Gracella</li><li>Glimmer</li><li>Cubrix</li><li>Galora</li><li>Chromea</li><li>Magazine</li></ul>
  <p class="abs news-txt">Become a part of our NEW ONE community!<br>INSIDER exclusive jewelry pieces can<br>win and never miss highlights.</p>
  <div class="abs email">Email Adress...</div>
  <div class="abs sub">SUBSCRIBE</div>
  <div class="abs copy">© 2013 lirvodune.com All Rights Reserved.</div>
  <div class="abs badge"></div>
</footer>
</body>
</html>
```